Seeking funky, innovative business cards

I am looking to refresh our current business cards to something more engaging, visual and impactful. We are a management consultancy firm, see website (www.larkstone-partners.com.au). I've included our colour scheme, sample of the slides we use and our old business cards. We would like our cards to have icons. The card should display:- Name- Title- Mobile number- Address- Email address- Website - Company logo- Our purpose statement "We create the best places on earth to work"

Contact Information for Business Card

Brennan Ulfsson
Consultant
0468 927 341
Level 3, 218 Wexley Street, Melbourne 3000
brennan@larkstone-partners.com.au
www.larkstone-partners.com.au

Purpose statement "we create the best places on earth to work"
LOGO available in google images

Font styles to use
Other font styles liked:
• Open Sans Light, Bebas Neue (open to other cool foints)

Colors
ffc214
5c5c5c
f5f5f5
fefefe

Requirements
Must have
• - Name
• - Title
• - Mobile number
• - Address
• - Email address
• - Website
• - Company logo
• - Our purpose statement "We create the best places on earth to work"
Nice to have
• - Icons
• - Colour (see our colour scheme"

```html
<!DOCTYPE html>
<html lang="en">
<head>
<meta charset="utf-8">
<title>Larkstone Partners — Business Card</title>
<link rel="stylesheet" href="https://fonts.googleapis.com/css2?family=Lato:wght@300;400&family=Open+Sans:wdth,wght@75..100,300..800&display=swap">
<style>
  :root {
    --brand-orange: #f8a832;
    --brand-yellow: #ffc214;
    --ink-dark: #4a4a4a;
    --ink-mid: #5c5c5c;
    --ink-soft: #7a7a7a;
    --paper: #fefefe;
    --backdrop: #e4e4e4;
  }
  * { margin: 0; padding: 0; box-sizing: border-box; }
  html, body { width: 1200px; height: 1200px; overflow: hidden; }
  body {
    background: var(--backdrop);
    position: relative;
    font-family: 'Lato', sans-serif;
  }
  .card {
    position: absolute;
    left: 226px;
    width: 780px;
    height: 451px;
    box-shadow: 0 6px 18px rgba(0,0,0,0.18);
  }
  .card--front { top: 106px; background: var(--brand-orange); }
  .card--back  { top: 638px; background: var(--paper); }

  .wordmark {
    position: absolute;
    display: flex;
    align-items: center;
    gap: 12px;
    font-family: 'Lato', sans-serif;
    font-weight: 300;
    font-size: 44px;
    letter-spacing: -0.5px;
    white-space: nowrap;
  }
  .wordmark__dot {
    width: 16px; height: 16px; border-radius: 50%;
    flex: none;
  }
  .card--front .wordmark {
    left: 0; right: 0; top: 190px; justify-content: center;
    color: var(--paper);
  }
  .card--front .wordmark__dot { background: var(--paper); }

  .purpose {
    position: absolute;
    left: 0; right: 0; top: 283px;
    text-align: center;
    font-family: 'Open Sans', sans-serif;
    font-stretch: 80%;
    font-weight: 700;
    font-size: 23px;
    color: var(--ink-dark);
    text-transform: uppercase;
  }

  .card--back .wordmark {
    right: 46px; top: 110px;
    color: var(--ink-dark);
  }
  .card--back .wordmark__dot { background: var(--brand-yellow); }

  .holder { position: absolute; left: 43px; top: 284px; }
  .holder__name { font-size: 28px; font-weight: 400; color: var(--ink-dark); line-height: 1.1; }
  .holder__title { font-size: 19px; color: var(--brand-yellow); margin-top: 4px; }
  .holder__rule { width: 93px; height: 2px; background: var(--brand-yellow); margin-top: 7px; }
  .holder__address { font-size: 18px; color: var(--ink-soft); margin-top: 13px; line-height: 24px; }

  .contact {
    position: absolute; right: 45px; top: 331px;
    list-style: none;
  }
  .contact__item {
    display: flex; align-items: center; justify-content: flex-end;
    gap: 10px; height: 27.5px;
    font-size: 18px; color: var(--ink-soft);
  }
  .contact__icon { width: 20px; height: 20px; flex: none; }
</style>
</head>
<body>

  <section class="card card--front" aria-label="Card front">
    <div class="wordmark"><span class="wordmark__dot"></span>Larkstone Partners</div>
    <p class="purpose">We create the best places on earth to work!</p>
  </section>

  <section class="card card--back" aria-label="Card back">
    <div class="wordmark"><span class="wordmark__dot"></span>Larkstone Partners</div>

    <div class="holder">
      <h1 class="holder__name">Brennan Ulfsson</h1>
      <p class="holder__title">Consultant</p>
      <div class="holder__rule"></div>
      <p class="holder__address">Level 3, 218 Wexley Street<br>Melbourne 3000</p>
    </div>

    <ul class="contact">
      <li class="contact__item">0468 927 341
        <svg class="contact__icon" viewBox="0 0 20 20" aria-hidden="true">
          <circle cx="10" cy="10" r="10" fill="var(--brand-orange)"/>
          <path d="M7 5.5c.6 0 1.6 2 1.6 2.4 0 .5-.9.9-.9 1.4 0 .8 1.7 2.6 2.5 2.7.5 0 .9-.9 1.4-.9.4 0 2.4 1 2.4 1.6 0 .9-1 1.8-1.9 1.8C9.5 14.5 5.5 10.5 5.5 7.4c0-.9.8-1.9 1.5-1.9z" fill="#fff"/>
        </svg>
      </li>
      <li class="contact__item">brennan@larkstone-partners.com.au
        <svg class="contact__icon" viewBox="0 0 20 20" aria-hidden="true">
          <circle cx="10" cy="10" r="10" fill="var(--brand-orange)"/>
          <rect x="5" y="6.5" width="10" height="7" rx="1" fill="#fff"/>
          <path d="M5.5 7l4.5 3.5L14.5 7" fill="none" stroke="var(--brand-orange)" stroke-width="1"/>
        </svg>
      </li>
      <li class="contact__item">www.larkstone-partners.com.au
        <svg class="contact__icon" viewBox="0 0 20 20" aria-hidden="true">
          <circle cx="10" cy="10" r="10" fill="var(--brand-orange)"/>
          <g fill="none" stroke="#fff" stroke-width="1">
            <circle cx="10" cy="10" r="5"/>
            <ellipse cx="10" cy="10" rx="2.2" ry="5"/>
            <path d="M5 10h10M6 7.5h8M6 12.5h8"/>
          </g>
        </svg>
      </li>
    </ul>
  </section>

</body>
</html>
```